Innovative Web Application Welcome Page with Free Trial and Embedded Video

We run the Kestrel Defence Orchestration Suite (https://kestrel.marrowbyte.example), which is the world's first security automation cloud that delivers automated security to organisations.Our existing Welcome page (page shown after login) needs redesigning to be inline with our new Kestrel brand (i.e. the Kestrel website - innovative and global). The Welcome Page will promote a 30-day trial of our Proactive Breached Login Sentinel feature. Screenshots attached including current Welcome Page, mock up of new Welcome Page content, Kestrel logos, Kestrel brochures, Kestrel main brand hero image, slide images, etc. The application header and side menu must remain the same. The design is for the main section of this page.

Target Market(s)

IT Security

Number of Pages Required

1 page

Font styles to use
Sans Serif
Other font styles liked:
• Website creative specifications sheet attached

Colors

Designer to choose only greyscale colors for use in the design.

Requirements
Must have
• All sections and text in the mockup image provided

```html
<!DOCTYPE html>
<html lang="en">
<head>
<meta charset="utf-8">
<title>Kestrel – Welcome</title>
<link href="https://fonts.googleapis.com/css2?family=Mulish:wght@400;600;700;800&display=swap" rel="stylesheet">
<style>
  :root {
    --header-bg: #1d232b;
    --sidebar-bg: #2b3139;
    --brand-red: #e02727;
    --ring: rgba(255,255,255,0.18);
    --panel-grey: #ececec;
    --ink: #1d232b;
    --white: #ffffff;
    --text-dark: #2a2a2a;
  }
  * { box-sizing: border-box; margin: 0; padding: 0; }
  html, body { width: 1200px; height: 852px; overflow: hidden; }
  body { font-family: "Mulish", Arial, sans-serif; background: var(--header-bg); position: relative; color: var(--white); }

  .app-header { position: absolute; left: 0; top: 0; width: 1200px; height: 80px; background: var(--header-bg); }
  .brand-name { position: absolute; left: 18px; top: 18px; font-size: 38px; font-weight: 400; letter-spacing: 1px; color: var(--white); line-height: 1; }
  .user-menu { position: absolute; right: 240px; top: 20px; text-align: right; font-size: 13px; line-height: 20px; }
  .user-menu strong, .lang-menu strong { font-weight: 700; }
  .caret { display: inline-block; width: 0; height: 0; border-left: 4px solid transparent; border-right: 4px solid transparent; border-top: 5px solid var(--white); margin-left: 4px; vertical-align: middle; }
  .avatar { position: absolute; left: 970px; top: 22px; width: 36px; height: 36px; border-radius: 50%; background: linear-gradient(135deg,#8a8f86,#5a5f58); }
  .lang-menu { position: absolute; left: 1034px; top: 20px; font-size: 13px; line-height: 20px; text-align: center; }
  .flag { position: absolute; left: 1102px; top: 21px; width: 38px; height: 38px; border-radius: 50%; background: linear-gradient(180deg,#d8d8d8,#9a9a9a); }

  .side-menu { position: absolute; left: 0; top: 80px; width: 166px; height: 772px; background: var(--sidebar-bg); }
  .profile-banner { height: 124px; background: linear-gradient(135deg,#5e5e5e,#2d2d2d 70%); position: relative; border-bottom: 1px solid #444a52; }
  .profile-banner span { position: absolute; left: 20px; bottom: 16px; font-size: 12px; font-weight: 700; }
  .menu-list { list-style: none; margin-top: 15px; }
  .menu-item { height: 41.6px; display: flex; align-items: center; padding: 0 12px 0 13px; font-size: 12.5px; }
  .menu-item svg { width: 15px; height: 15px; margin-right: 7px; fill: var(--white); flex: none; }
  .menu-item .label { flex: 1; }
  .menu-item .chev { width: 5px; height: 5px; border-top: 1.5px solid var(--white); border-right: 1.5px solid var(--white); transform: rotate(45deg); }

  .main-stage { position: absolute; left: 166px; top: 80px; width: 1034px; height: 722px; overflow: hidden; background: var(--panel-grey); }
  .main-stage > svg { position: absolute; left: 0; top: 0; }

  .trial-promo { position: absolute; left: 592px; top: 64px; width: 415px; }
  .trial-promo h2 { font-size: 25px; font-weight: 800; line-height: 1.2; margin-bottom: 8px; }
  .trial-promo p { font-size: 12px; line-height: 25.6px; text-align: justify; }
  .btn-dark { display: inline-block; width: 163px; height: 46px; line-height: 46px; text-align: center; background: var(--ink); color: var(--white); font-size: 16px; font-weight: 800; letter-spacing: -0.2px; }
  .trial-promo .btn-dark { margin-top: 18px; }

  .welcome-intro { position: absolute; left: 33px; top: 480px; width: 404px; }
  .welcome-intro h1 { font-size: 25px; font-weight: 800; line-height: 1.2; }
  .welcome-intro p { font-size: 15px; line-height: 28px; text-align: justify; }
  .welcome-intro .btn-dark { margin-top: 4px; }

  .video-card { position: absolute; left: 591px; top: 385px; width: 381px; }
  .video-frame { height: 193px; position: relative; overflow: hidden; background: var(--brand-red); }
  .video-frame svg { position: absolute; left: 0; top: 0; }
  .video-kicker { position: absolute; left: 120px; top: 115px; width: 66px; text-align: right; font-size: 11px; line-height: 1; color: var(--white); }
  .video-title { position: absolute; left: 193px; top: 98px; color: var(--white); font-size: 46px; font-weight: 400; line-height: 1; }
  .video-card h3 { color: var(--text-dark); font-size: 16.5px; font-weight: 700; margin-top: 14px; }
  .video-card p { color: var(--text-dark); font-size: 12px; line-height: 22.5px; margin-top: 6px; }
  .link-red { color: var(--brand-red); font-size: 16px; font-weight: 800; display: block; margin-top: 6px; }

  .app-footer { position: absolute; left: 166px; top: 802px; width: 1034px; height: 50px; background: var(--header-bg); text-align: center; font-size: 13px; line-height: 50px; }
</style>
</head>
<body>
<header class="app-header">
  <div class="brand-name">Kestrel</div>
  <div class="user-menu">Welcome<br><strong>Rowan</strong><span class="caret"></span></div>
  <div class="avatar" role="img" aria-label="User profile photo"></div>
  <div class="lang-menu">Language<br><strong>English</strong><span class="caret"></span></div>
  <div class="flag" role="img" aria-label="Selected language flag"></div>
</header>

<nav class="side-menu">
  <div class="profile-banner" role="img" aria-label="Profile banner photo of two oryx clashing"><span>Rowan</span></div>
  <ul class="menu-list">
    <li class="menu-item"><svg viewBox="0 0 16 16"><circle cx="6" cy="7" r="4"/><circle cx="12.5" cy="11.5" r="2.5"/></svg><span class="label">Automation</span><i class="chev"></i></li>
    <li class="menu-item"><svg viewBox="0 0 16 16"><rect x="1" y="5" width="14" height="4"/><rect x="2" y="9" width="12" height="6"/></svg><span class="label">Marketplace</span><i class="chev"></i></li>
    <li class="menu-item"><svg viewBox="0 0 16 16"><circle cx="8" cy="5" r="3.5"/><circle cx="4.5" cy="11" r="3.5"/><circle cx="11.5" cy="11" r="3.5"/></svg><span class="label">Workflows</span><i class="chev"></i></li>
    <li class="menu-item"><svg viewBox="0 0 16 16"><path d="M8 1l7 3.5v7L8 15l-7-3.5v-7z"/></svg><span class="label">Modules</span><i class="chev"></i></li>
    <li class="menu-item"><svg viewBox="0 0 16 16"><rect x="1" y="2" width="6" height="4"/><rect x="10" y="2" width="5" height="4"/><rect x="6" y="10" width="5" height="4"/><rect x="3" y="6" width="2" height="6"/></svg><span class="label">Services</span><i class="chev"></i></li>
    <li class="menu-item"><svg viewBox="0 0 16 16"><path d="M1 3h5l2 2h7v9H1z"/></svg><span class="label">Containers</span><i class="chev"></i></li>
    <li class="menu-item"><svg viewBox="0 0 16 16"><rect x="1" y="1" width="6" height="6"/><rect x="9" y="1" width="6" height="6"/><rect x="1" y="9" width="6" height="6"/><rect x="9" y="9" width="6" height="6"/></svg><span class="label">Dashboards</span><i class="chev"></i></li>
    <li class="menu-item"><svg viewBox="0 0 16 16"><path d="M1 2h1.5v11H15v1.5H1z"/><path d="M3 11l4-5 3 3 4-5 1 1-5 6-3-3-3 4z"/></svg><span class="label">Charts</span><i class="chev"></i></li>
    <li class="menu-item"><svg viewBox="0 0 16 16"><circle cx="8" cy="4.5" r="3.5"/><path d="M2 15c0-4 2.5-6 6-6s6 2 6 6z"/></svg><span class="label">Agents</span><i class="chev"></i></li>
    <li class="menu-item"><svg viewBox="0 0 16 16"><path d="M4 7V5a4 4 0 018 0v2h1v8H3V7zm2 0h4V5a2 2 0 00-4 0z"/></svg><span class="label">Credentials</span><i class="chev"></i></li>
    <li class="menu-item"><svg viewBox="0 0 16 16"><path d="M4 7V5a4 4 0 018 0v2h1v8H3V7zm2 0h4V5a2 2 0 00-4 0z"/></svg><span class="label">Security Zones</span><i class="chev"></i></li>
    <li class="menu-item"><svg viewBox="0 0 16 16"><rect x="2" y="3" width="12" height="12"/><rect x="4" y="1" width="2" height="3"/><rect x="10" y="1" width="2" height="3"/></svg><span class="label">Events</span><i class="chev"></i></li>
    <li class="menu-item"><svg viewBox="0 0 16 16"><circle cx="6" cy="4.5" r="3.5"/><path d="M0 15c0-4 2.5-6 6-6s6 2 6 6z"/><circle cx="13" cy="12" r="2.5"/></svg><span class="label">Security Services</span><i class="chev"></i></li>
  </ul>
</nav>

<main class="main-stage">
  <svg width="1034" height="722" viewBox="0 0 1034 722">
    <defs>
      <linearGradient id="heroTone" x1="0" y1="0" x2="1" y2="0">
        <stop offset="0" stop-color="#c81e1e"/>
        <stop offset="0.55" stop-color="#d42424"/>
        <stop offset="0.62" stop-color="#6a6a6a"/>
        <stop offset="1" stop-color="#2a2a2a"/>
      </linearGradient>
      <clipPath id="clipTopRed"><polygon points="444,0 1034,0 1034,360 588,360"/></clipPath>
      <clipPath id="clipBottomRed"><polygon points="0,360 588,360 444,722 0,722"/></clipPath>
    </defs>
    <polygon points="0,0 444,0 588,360 0,360" fill="url(#heroTone)" role="img" aria-label="Hero photo of two oryx clashing, red and greyscale"/>
    <polygon points="444,0 1034,0 1034,360 588,360" fill="var(--brand-red)"/>
    <circle cx="766" cy="180" r="156" fill="none" stroke="var(--ring)" stroke-width="32" clip-path="url(#clipTopRed)"/>
    <polygon points="0,360 588,360 444,722 0,722" fill="var(--brand-red)"/>
    <circle cx="206" cy="540" r="156" fill="none" stroke="var(--ring)" stroke-width="32" clip-path="url(#clipBottomRed)"/>
    <polyline points="444,0 588,360 444,722" fill="none" stroke="var(--white)" stroke-width="3"/>
    <line x1="0" y1="360" x2="588" y2="360" stroke="var(--white)" stroke-width="1"/>
  </svg>

  <section class="trial-promo">
    <h2>MITIGATE YOUR #1 CYBER RISK</h2>
    <p>Lorem ipsum dolor sit amet, consectetur adipiscing elit, sed do eiusmod tempor incididunt ut labore et dolore magna aliqua. Quis ipsum suspendisse ultrices gravida.</p>
    <p>Sed ut perspiciatis unde omnis iste natus error sit voluptatem accusantium doloremque laudantium, dicta sunt explicabo.</p>
    <a class="btn-dark">30-DAY TRIAL</a>
  </section>

  <section class="welcome-intro">
    <h1>WELCOME TO KESTREL</h1>
    <p>Lorem ipsum dolor sit amet, consectetur adipiscing elit, sed do eiusmod tempor incididunt ut labore et dolore magna aliqua. Quis ipsum suspendisse ultrices gravida. Risus commodo viverra maecenas accumsan lacus vel facilisis.</p>
    <a class="btn-dark">READ MORE</a>
  </section>

  <section class="video-card">
    <div class="video-frame" role="img" aria-label="Getting started with Kestrel video">
      <svg width="381" height="193" viewBox="0 0 381 193"><polygon points="175,0 381,0 381,193 252,193" fill="#000"/></svg>
      <span class="video-kicker">GETTING<br>STARTED<br>WITH</span>
      <span class="video-title">Kestrel</span>
    </div>
    <h3>SED UT PERSPICIATIS UNDE OMNIS ISTE</h3>
    <p>Sed ut perspiciatis unde omnis iste natus error sit voluptatem accusantium doloremque laudantium, totam rem aperiam, eaque ipsa quae ab illo inventore veritatis et sunt explicabo.</p>
    <a class="link-red">READ MORE</a>
  </section>
</main>

<footer class="app-footer">Copyrights @ 2019 All Rights Reserved</footer>
</body>
</html>
```